Boutique town planning business needs a Business Card design

We need a business card design for a new company called The Zoning Bridgeway. We provide town planning and urban design services to government, business and community groups. We would like to see the designs use the colours in the logo (blue, deep red, green and amber), plenty of white and including black and grey in the writing. The final design should communicate collaboration, creativity and professionalism and that we are approachable.

Industry/Entity Type

Town

```html
<!DOCTYPE html>
<html lang="en">
<head>
<meta charset="utf-8">
<title>The Zoning Bridgeway – Business Card</title>
<link rel="stylesheet" href="https://fonts.googleapis.com/css2?family=Cinzel:wght@400;600&family=Open+Sans:wght@400;600&display=swap">
<style>
  :root {
    --backdrop: #e4e2de;
    --card-white: #f2f2f2;
    --ink-black: #0b0b0b;
    --ink-grey: #5a5a5a;
    --rule-grey: #9a9a9a;
    --brand-blue: #3f8fbf;
    --brand-green: #6fa83a;
    --brand-amber: #e39a1f;
    --brand-red: #b8342a;
  }
  * { box-sizing: border-box; margin: 0; padding: 0; }
  html, body {
    width: 1200px; height: 900px; overflow: hidden;
    background: var(--backdrop);
    font-family: "Open Sans", Arial, sans-serif;
  }
  .canvas {
    position: relative; width: 1200px; height: 900px;
    display: flex; flex-direction: column; align-items: center; justify-content: center; gap: 48px;
  }
  .card {
    position: relative; width: 660px; height: 377px; overflow: hidden;
    box-shadow: 0 2px 8px rgba(0,0,0,.18);
  }

  /* Back side */
  .card-back { background: var(--ink-black); }
  .card-back .wordmark {
    position: absolute; left: 50%; top: 50%; transform: translate(-50%, -50%);
    display: flex; align-items: center; gap: 14px;
  }
  .wordmark { display: flex; align-items: center; gap: 12px; }
  .wordmark-dot { width: 38px; height: 38px; border-radius: 50%; background: var(--brand-blue); flex: none; }
  .wordmark-name { font-size: 26px; font-weight: 600; letter-spacing: -.3px; white-space: nowrap; }
  .card-back .wordmark-name { color: #d8d8d8; }

  /* Front side */
  .card-front { background: var(--card-white); }
  .colour-corner { position: absolute; left: 0; top: 0; width: 60px; height: 377px; }

  .contact-block { position: absolute; left: 80px; top: 44px; width: 270px; }
  .person-name {
    font-family: "Cinzel", Georgia, serif; font-size: 19px; font-weight: 600;
    letter-spacing: 1.6px; color: #333; padding-bottom: 6px;
    border-bottom: 1px solid var(--rule-grey);
  }
  .credentials { margin-top: 7px; font-size: 11px; color: var(--ink-grey); }
  .job-title { font-size: 11px; color: var(--ink-grey); margin-top: 1px; }
  .contact-list { list-style: none; margin-top: 12px; }
  .contact-list li { font-size: 12px; color: var(--ink-grey); line-height: 1.7; display: flex; gap: 12px; }
  .contact-label { color: var(--brand-red); font-weight: 600; width: 10px; }

  .card-front .wordmark { position: absolute; left: 360px; top: 150px; }
  .card-front .wordmark-dot { width: 34px; height: 34px; }
  .card-front .wordmark-name { color: #444; font-size: 22px; }

  .divider-rule { position: absolute; left: 300px; right: 0; top: 262px; height: 1px; background: var(--rule-grey); }

  .footer-band { position: absolute; left: 0; bottom: 0; width: 660px; height: 58px; }
  .abn { position: absolute; left: 236px; bottom: 20px; font-size: 12px; letter-spacing: 1.2px; color: #bdbdbd; }
</style>
</head>
<body>
<main class="canvas">

  <section class="card card-back" aria-label="Card back">
    <div class="wordmark">
      <span class="wordmark-dot"></span>
      <span class="wordmark-name">The Zoning Bridgeway</span>
    </div>
  </section>

  <section class="card card-front" aria-label="Card front">
    <svg class="colour-corner" viewBox="0 0 60 377" aria-hidden="true">
      <polygon points="0,0 52,0 42,94 0,94" fill="var(--brand-red)"/>
      <polygon points="0,94 42,94 32,188 0,188" fill="var(--brand-amber)"/>
      <polygon points="0,188 32,188 22,283 0,283" fill="var(--brand-green)"/>
      <polygon points="0,283 22,283 12,377 0,377" fill="var(--brand-blue)"/>
    </svg>

    <div class="contact-block">
      <h1 class="person-name">Miranda Ashworth</h1>
      <p class="credentials">BPD (Urban Planning), GDipPD, MPIA, VPELA</p>
      <p class="job-title">Director</p>
      <ul class="contact-list">
        <li><span class="contact-label">M</span>0400 318 562</li>
        <li><span class="contact-label">E</span>zoningbridgeway@mailbox.com</li>
        <li><span class="contact-label">W</span>www.zoningbridgeway.com.au</li>
      </ul>
    </div>

    <div class="wordmark">
      <span class="wordmark-dot"></span>
      <span class="wordmark-name">The Zoning Bridgeway</span>
    </div>

    <div class="divider-rule"></div>

    <svg class="footer-band" viewBox="0 0 660 58" aria-hidden="true">
      <polygon points="190,0 660,0 660,58 190,58 212,29" fill="var(--ink-black)"/>
    </svg>
    <p class="abn">ABN 51824037196</p>
  </section>

</main>
</body>
</html>
```